Flat bootstrap design for existing site

I'm looking for a modern flat design based around an existing logo. This has to be a custom design (no external templates), and implemented into a bootstrap framework.

The logo is attached as 2 versions - choose whichever you want, that flows better with whatever design you choose.

Added screenshots of the existing site (currently using the default bootstrap layouts). Please make your designs around those pages in the screenshots (i.e. the homepage only has the postal code input and the header). The active page has 3 screenshots, because I wanted to illustrate the other states that would be visible (in the table rows).

This is a moving/junk removal website, just for some context.

Here's some example websites (flat designs) that I like, just to give you an idea of what I'm after.

https://www.plimvora.com/
https://dacklow.com/
https://trevanu.com/
https://quobrintal.com/en/

Coding

Coded - Design and coding required

Number of Pages Required

5+ page

Colors

Designer to choose colors to be used in the design.

Requirements
Must have
• It must be a modern/simple flat design, that is built around the existing logo (attached).
• It has to be implemented using bootstrap.

```html
<!DOCTYPE html>
<html lang="en">
<head>
<meta charset="utf-8">
<title>Haulvex – Book Details</title>
<link href="https://fonts.googleapis.com/css2?family=Mulish:wght@400;600;700;800&family=Open+Sans:wght@400;600&display=swap" rel="stylesheet">
<style>
  :root {
    --brand-blue: #47c6f3;
    --notice-blue: #8adcf7;
    --page-grey: #e6e6e6;
    --panel-white: #ffffff;
    --footer-grey: #f5f5f5;
    --text-dark: #222222;
    --text-body: #444444;
    --text-muted: #777777;
    --nav-text: #6b6b6b;
    --table-head: #eeeeee;
    --row-line: #c8c8c8;
    --badge-dark: #555555;
  }
  * { box-sizing: border-box; margin: 0; padding: 0; }
  html, body { width: 1200px; height: 1100px; overflow: hidden; }
  body { position: relative; background: var(--page-grey); font-family: 'Mulish', sans-serif; color: var(--text-body); }

  .site-header { position: absolute; left: 0; top: 0; width: 1200px; height: 114px; background: var(--panel-white); }
  .brand { position: absolute; left: 82px; top: 36px; display: flex; align-items: center; gap: 10px; }
  .brand-dot { width: 34px; height: 34px; border-radius: 50%; background: var(--brand-blue); }
  .brand-name { font-size: 40px; font-weight: 800; color: var(--brand-blue); letter-spacing: 1px; }
  .main-nav { position: absolute; top: 46px; left: 487px; display: flex; gap: 39px; font-size: 17px; color: var(--nav-text); letter-spacing: .3px; }
  .account { position: absolute; top: 46px; left: 951px; font-size: 15px; color: var(--nav-text); display: flex; align-items: center; gap: 6px; }

  .book-panel { position: absolute; left: 86px; top: 147px; width: 1027px; height: 362px; background: var(--brand-blue); color: #fff; }
  .book-title { position: absolute; left: 46px; top: 30px; font-size: 30px; font-weight: 700; }
  .field-label { position: absolute; font-size: 18px; font-weight: 600; }
  .field { position: absolute; height: 44px; background: #fff; box-shadow: 0 2px 4px rgba(0,0,0,.15); color: var(--text-muted); font-size: 16px; display: flex; align-items: center; justify-content: space-between; padding: 0 12px; }
  .update-btn { position: absolute; left: 42px; top: 278px; width: 156px; height: 47px; border: 3px solid #fff; border-radius: 24px; color: #fff; font-size: 18px; font-weight: 700; display: flex; align-items: center; justify-content: center; }

  .drivers-title { position: absolute; left: 93px; top: 551px; font-size: 30px; font-weight: 800; color: var(--text-muted); }
  .notice { position: absolute; left: 91px; top: 606px; width: 1028px; height: 48px; background: var(--notice-blue); color: #fff; font-size: 15.5px; padding: 14px 36px; }
  .drivers-card { position: absolute; left: 91px; top: 654px; width: 1028px; height: 315px; background: var(--panel-white); }
  .table-head { position: absolute; left: 28px; top: 19px; width: 957px; height: 39px; background: var(--table-head); font-size: 16px; color: var(--text-dark); font-weight: 600; }
  .cell { position: absolute; }
  .table-row { position: absolute; left: 36px; width: 960px; height: 48px; font-family: 'Open Sans', sans-serif; font-size: 14px; color: var(--text-body); }
  .table-row.divided { border-bottom: 1px solid var(--row-line); }
  .status { position: absolute; left: 791px; width: 108px; height: 26px; background: var(--badge-dark); color: #fff; font-size: 13px; display: flex; align-items: center; justify-content: center; }

  .site-footer { position: absolute; left: 0; top: 1018px; width: 1200px; height: 82px; background: var(--footer-grey); text-align: center; font-size: 15px; color: var(--text-muted); padding-top: 26px; }
</style>
</head>
<body>
  <header class="site-header">
    <div class="brand"><span class="brand-dot"></span><span class="brand-name">HAULVEX</span></div>
    <nav class="main-nav"><span>BOOK</span><span>HOW IT WORKS</span><span>BECOME A DRIVER</span></nav>
    <div class="account">george@mailvanto.com
      <svg width="16" height="10" viewBox="0 0 16 10"><path d="M1 1l7 7 7-7" fill="none" stroke="#6b6b6b" stroke-width="1.6"/></svg>
    </div>
  </header>

  <section class="book-panel">
    <h1 class="book-title">Book Details</h1>
    <span class="field-label" style="left:44px;top:82px">Package Selected:</span>
    <span class="field-label" style="left:522px;top:82px">Pick-up time selected</span>
    <div class="field" style="left:44px;top:113px;width:465px">Package 1
      <svg width="18" height="10" viewBox="0 0 18 10"><path d="M1 1l8 8 8-8" fill="none" stroke="#777" stroke-width="1.6"/></svg>
    </div>
    <div class="field" style="left:522px;top:113px;width:465px">July 18 at 4:13 am
      <svg width="18" height="18" viewBox="0 0 18 18"><rect x="1" y="3" width="16" height="14" fill="none" stroke="#999" stroke-width="1.2"/><path d="M1 7h16M5 1v4M13 1v4M5 10h2M9 10h2M13 10h1M5 13h2M9 13h2M13 13h1" stroke="#999" stroke-width="1.2"/></svg>
    </div>
    <span class="field-label" style="left:46px;top:178px">Description</span>
    <div class="field" style="left:46px;top:209px;width:941px">1 Large stove</div>
    <div class="update-btn">Update</div>
  </section>

  <h2 class="drivers-title">Drivers in your area</h2>
  <div class="notice">Please stay on this page and be patient, while we contact the driver and find you one ASAP</div>

  <section class="drivers-card">
    <div class="table-head">
      <span class="cell" style="left:21px;top:9px">Name</span>
      <span class="cell" style="left:199px;top:9px">Distance</span>
      <span class="cell" style="left:399px;top:9px">Agreed pick-up time</span>
    </div>
    <div class="table-row divided" style="top:68px">
      <span class="cell" style="left:2px;top:12px">Dale Morrow</span>
      <span class="cell" style="left:176px;top:12px">4.04 km away</span>
      <span class="cell" style="left:389px;top:8px">-</span>
      <span class="status" style="top:7px">Pending</span>
    </div>
    <div class="table-row divided" style="top:116px">
      <span class="cell" style="left:2px;top:12px">Owen Hartley</span>
      <span class="cell" style="left:176px;top:12px">5.75 km away</span>
      <span class="cell" style="left:389px;top:8px">-</span>
      <span class="status" style="top:10px">Pending</span>
    </div>
    <div class="table-row divided" style="top:164px;height:53px">
      <span class="cell" style="left:2px;top:12px">Miles Brandt</span>
      <span class="cell" style="left:176px;top:12px">11.13 km away</span>
      <span class="cell" style="left:389px;top:8px">-</span>
      <span class="status" style="top:12px">Pending</span>
    </div>
    <div class="table-row" style="top:217px">
      <span class="cell" style="left:2px;top:10px">Reid Calloway</span>
      <span class="cell" style="left:176px;top:10px">11.91 km away</span>
      <span class="cell" style="left:389px;top:6px">-</span>
      <span class="status" style="top:12px">Pending</span>
    </div>
  </section>

  <footer class="site-footer">© 2017 Company Name&nbsp; All right reserved&nbsp; Term of Use</footer>
</body>
</html>
```